Business Card Design

I give lessons and clinics for dressage riders
I would like the design to be an outline (with broad lines) of a dressage horse and rider with in background of whole card with print over top tan or parchment card with burgundy print

Industry/Entity Type

Business

Contact Information for Business Card

Dale Ferrin
612-374-2059
Classical dressage training for the modern American
Clinics, lessons, training level -Prix St. George

Requirements
Must have
• broad lined outline of dressage horse and rider

```html
<!DOCTYPE html>
<html lang="en">
<head>
<meta charset="utf-8">
<title>Dale Ferrin – Business Card</title>
<link rel="stylesheet" href="https://fonts.googleapis.com/css2?family=Cinzel:wght@400;500&family=Arimo:wght@400&display=swap">
<style>
  :root {
    --page-bg: #e6e1d8;
    --card-bg: #f3e7cf;
    --ink: #6e1a26;
    --band-dark: #6e1a26;
    --band-edge: #e3d3b3;
    --figure-light: rgba(110, 26, 38, 0.04);
    --figure-mid: rgba(110, 26, 38, 0.12);
  }
  html, body {
    margin: 0;
    width: 1200px;
    height: 800px;
    overflow: hidden;
    background: var(--page-bg);
  }
  .canvas {
    position: relative;
    width: 1200px;
    height: 800px;
    display: flex;
    align-items: center;
    justify-content: center;
  }
  .card {
    position: relative;
    width: 1050px;
    height: 600px;
    background: var(--card-bg);
    overflow: hidden;
    box-shadow: 0 6px 24px rgba(0,0,0,0.15);
  }
  .card__band {
    position: absolute;
    inset: 0;
    width: 100%;
    height: 100%;
  }
  .card__figure {
    position: absolute;
    left: 130px;
    top: 30px;
    width: 360px;
    height: 420px;
    background: radial-gradient(ellipse 50% 50% at 50% 50%, var(--figure-mid) 0%, var(--figure-light) 60%, rgba(243,231,207,0) 100%);
  }
  .card__info {
    position: absolute;
    left: 590px;
    top: 70px;
    color: var(--ink);
  }
  .card__name {
    margin: 0;
    font-family: "Cinzel", serif;
    font-weight: 500;
    font-size: 44px;
    letter-spacing: 2px;
    white-space: nowrap;
  }
  .card__phone {
    margin: 14px 0 0;
    font-family: "Arimo", sans-serif;
    font-size: 27px;
    letter-spacing: 1px;
  }
  .card__services {
    margin: 30px 0 0;
    padding: 0;
    list-style: none;
    font-family: "Arimo", sans-serif;
    font-size: 22px;
    line-height: 1.3;
    white-space: nowrap;
  }
</style>
</head>
<body>
  <main class="canvas">
    <section class="card">
      <div class="card__figure" role="img" aria-label="Faint broad-lined outline of a dressage horse and rider"></div>
      <svg class="card__band" viewBox="0 0 1050 600" preserveAspectRatio="none" aria-hidden="true">
        <path d="M0 385 C 250 395, 600 430, 1050 485 L1050 600 L0 600 Z" fill="var(--band-edge)"/>
        <path d="M0 405 C 250 415, 600 450, 1050 505 L1050 600 L0 600 Z" fill="var(--band-dark)"/>
      </svg>
      <div class="card__info">
        <h1 class="card__name">Dale Ferrin</h1>
        <p class="card__phone">612-374-2059</p>
        <ul class="card__services">
          <li>Classical dressage training for the</li>
          <li>modern American</li>
          <li>Clinics</li>
          <li>lessons</li>
          <li>training level</li>
          <li>Prix St. George</li>
        </ul>
      </div>
    </section>
  </main>
</body>
</html>
```